Request for Business Card Design

Hi. My name is Marlene, I am looking for a new business card design for my company, Quarrow Signal Instruments, LLC. I really like the design you did for Tarsel Venture and was hoping you could do something similar using our full logo and our mark. I am also open to any raised texture design using our mark. I have attached our full logo, which would need to be somewhere on the card, as well as the mark in both outline and full form, as well as our brand colors / guide. The card does not have to be white, as long as our logo and mark appear. I actually like darker colored business cards more, but am open to all options. If you are interested in working with me, please let me know. We would also take the business card design into letterhead design if you can do that.

```html
<!DOCTYPE html>
<html lang="en">
<head>
<meta charset="utf-8">
<title>Quarrow Signal Instruments — Business Card</title>
<link rel="stylesheet" href="https://fonts.googleapis.com/css2?family=Lato:wght@400;700;900&display=swap">
<style>
  :root {
    --backdrop: #2a2a2c;
    --card: #303032;
    --card-edge: #3a3a3d;
    --brand-blue: #0b9ccc;
    --silver: #c9c9cc;
    --text-light: #d6d6d8;
    --text-muted: #8d8d91;
  }
  * { margin: 0; padding: 0; box-sizing: border-box; }
  html, body {
    width: 1200px; height: 799px; overflow: hidden;
    background: var(--backdrop);
    font-family: "Lato", Arial, sans-serif;
  }
  .canvas {
    position: relative; width: 1200px; height: 799px;
    display: flex; align-items: center; justify-content: center; gap: 60px;
  }
  .card {
    position: relative; width: 500px; height: 286px;
    background: var(--card);
    border: 1px solid var(--card-edge);
  }
  /* Front */
  .card--front { display: flex; align-items: center; justify-content: center; gap: 18px; }
  .brand-dot {
    width: 44px; height: 44px; border-radius: 50%;
    background: var(--brand-blue);
  }
  .brand-name {
    font-weight: 700; font-size: 26px; letter-spacing: 3px;
    text-transform: uppercase; color: var(--silver);
  }
  /* Back */
  .card--back { padding: 0; }
  .emboss-ring {
    position: absolute; left: 42px; top: 40px;
    width: 150px; height: 150px; border-radius: 50%;
    border: 1.5px solid #6e6e72;
  }
  .contact {
    position: absolute; right: 34px; bottom: 30px;
    text-align: right; color: var(--text-light);
  }
  .contact__name {
    font-weight: 900; font-size: 26px; letter-spacing: 1px;
    text-transform: uppercase; color: var(--brand-blue); line-height: 1;
  }
  .contact__role { font-size: 14px; color: var(--text-muted); margin: 4px 0 10px; }
  .contact__line {
    display: flex; justify-content: flex-end; align-items: center; gap: 8px;
    font-size: 11.5px; line-height: 17px;
  }
  .contact__line svg { width: 10px; height: 10px; fill: var(--brand-blue); }
  .contact__company { font-weight: 700; font-size: 12px; color: var(--brand-blue); margin-top: 6px; }
  .contact__address { font-size: 11.5px; }
</style>
</head>
<body>
<main class="canvas">
  <section class="card card--front" aria-label="Card front">
    <span class="brand-dot"></span>
    <span class="brand-name">Quarrow Signal Instruments</span>
  </section>

  <section class="card card--back" aria-label="Card back">
    <div class="emboss-ring"></div>
    <div class="contact">
      <p class="contact__name">Daniel Reyes</p>
      <p class="contact__role">Founder &amp; CEO</p>
      <p class="contact__line">+001 555 014 2270
        <svg viewBox="0 0 10 10"><path d="M2 0.5 L3.6 0.5 L4.2 2.8 L3 3.7 Q4 6 6.3 7 L7.2 5.8 L9.5 6.4 L9.5 8 Q9.5 9.5 8 9.5 Q0.5 9 0.5 2 Q0.5 0.5 2 0.5Z"/></svg></p>
      <p class="contact__line">+001 555 014 2291
        <svg viewBox="0 0 10 10"><rect x="2.5" y="0.5" width="5" height="3"/><rect x="0.5" y="3.5" width="9" height="4" rx="1"/><rect x="2.5" y="6.5" width="5" height="3"/></svg></p>
      <p class="contact__line">marlene@quarrowsignal.com
        <svg viewBox="0 0 10 10"><rect x="0.5" y="1.5" width="9" height="7"/><path d="M0.5 1.5 L5 5.5 L9.5 1.5" stroke="#303032" stroke-width="1" fill="none"/></svg></p>
      <p class="contact__line">quarrowsignal.com
        <svg viewBox="0 0 10 10"><circle cx="5" cy="5" r="4.5"/><path d="M0.5 5 H9.5 M5 0.5 Q2 5 5 9.5 Q8 5 5 0.5" stroke="#303032" stroke-width="0.8" fill="none"/></svg></p>
      <p class="contact__company">Quarrow Signal Instruments, LLC</p>
      <p class="contact__address">1180 Harbor Ridge Road, Fenwick, CO 80999</p>
    </div>
  </section>
</main>
</body>
</html>
```